Vietnam Motorcycle Trip TRAVEL GUIDE!! Book Cover!

I need an adventurous book cover for a book called "THROTTLE MERIDIAN: A Wanderer's Manual for Crossing the Breadth of Vietnam". I would like people to look at the cover and think adventure and Vietnam. I want it to appeal to backpackers and people who have not travelled to Vietnam. A motorbike riding along a road in Vietnam would be ideal with some landscapes to suggest we are definitely in Vietnam. The rear cover could perhaps be one of Vietnam's tropical beaches or something else that says "this place is a paradise". It could also be something else that is quinessentially Vietnamese.

The book will be A5 Dimensions. And it will also need a printable A5 interior cover too. The interior covers can just be images. No text needed. These interior images can be motorcycle related or Vietnam related. Perhaps some images of Vietnam or some Pho or Banh Mi to give it a bit of flavour. Or a long open road with a motorbike on it.

Please leave space in the external rear, lower right hand corner for a barcode.

I've attached some images to gain inspiration from. And a sample chapter.

Colours I'd like to see on there - greens, camoflague perhaps, yellow, brown, blue.

Target Market(s)

Male backpackers aged 18-35 years old. New Zealand and Australian travellers.

Font styles to use
Serif
Sans Serif

Requirements
Must have
• Exterior and Interior covers.
Barcode space.
Title and subtitle.
Synopsis on rear cover.
Exciting title fonts - perhaps Brushstroke or something equally exciting and rugged
Nice to have
• Colours I'd like to see on there - greens, camoflague perhaps, yellow, brown, blue.

A motorbike riding on the open road of Vietnam.

Rice paddies, beaches, Korvan Conflict stuff perhaps.

A New Zealand Flag
A Vietnam Flag
Should not have
• Scenery from countries outside Southeast Asia

```html
<!DOCTYPE html>
<html lang="en">
<head>
<meta charset="utf-8">
<title>Throttle Meridian – Cover Spread</title>
<link rel="stylesheet" href="https://fonts.googleapis.com/css2?family=Permanent+Marker&family=Lato:wght@400;700&family=Oswald:wght@600&display=swap">
<style>
  :root {
    --canvas: #262626;
    --cover-yellow: #f6d81a;
    --cover-yellow-deep: #d9b80f;
    --olive-shadow: #8f8220;
    --title-blue: #1565c0;
    --ink: #111111;
    --spine: #2a2a2a;
    --spine-text: #f2f2f2;
    --band-olive: #8a7d4a;
    --leaf-green: #5f8f34;
    --road-teal: #2d5a55;
    --author-yellow: #f5dc1c;
    --flag-red: #da251d;
    --flag-blue: #1f4aa0;
    --rule: #222222;
  }
  * { box-sizing: border-box; margin: 0; padding: 0; }
  html, body { width: 850px; height: 1200px; overflow: hidden; background: var(--canvas); }
  .spread {
    position: absolute; left: 22px; top: 325px;
    width: 806px; height: 549px; display: flex;
  }
  /* Back cover */
  .back-cover {
    position: relative; width: 383px; height: 100%;
    background: var(--cover-yellow);
    font-family: "Lato", sans-serif; color: var(--ink);
    overflow: hidden;
  }
  .back-photo {
    position: absolute; left: 0; right: 0; bottom: 0; height: 230px;
    background: linear-gradient(to bottom, rgba(246,216,26,0) 0%, rgba(190,160,20,0.55) 60%, rgba(150,125,20,0.7) 100%);
  }
  .back-content { position: absolute; left: 23px; top: 24px; width: 337px; }
  .back-headline {
    font-size: 19.5px; line-height: 24px; font-weight: 400; text-align: right;
    letter-spacing: -0.3px; text-transform: uppercase;
  }
  .back-headline strong { color: var(--title-blue); font-weight: 700; }
  .synopsis { font-size: 7.3px; line-height: 9.4px; text-align: justify; margin-top: 9px; }
  .synopsis + .synopsis { margin-top: 9px; }
  .reveals-heading { color: var(--title-blue); font-size: 9px; margin-top: 9px; text-transform: uppercase; }
  .reveal-list { list-style: none; margin-top: 5px; }
  .reveal-list li {
    font-size: 8.4px; line-height: 10px; font-weight: 700; padding: 5px 0 4px 10px;
    border-bottom: 1px solid var(--rule); position: relative; text-align: justify;
  }
  .reveal-list li::before { content: "•"; position: absolute; left: 1px; top: 5px; }
  .closing { font-size: 7.3px; line-height: 9.4px; margin-top: 8px; }
  .paradise {
    font-family: "Permanent Marker", cursive; font-size: 24px; text-align: right;
    margin-top: 18px; letter-spacing: 0.5px; transform: skewX(-6deg);
  }
  .flags { position: absolute; right: 23px; top: 408px; display: flex; gap: 0; }
  .flag { width: 33px; height: 20px; display: block; }
  .site { position: absolute; right: 23px; top: 431px; font-size: 8.5px; font-weight: 700; color: #1e5aa8; letter-spacing: 0.3px; }
  .genre { position: absolute; right: 23px; top: 446px; font-size: 6.5px; letter-spacing: 0.6px; color: #555; }
  .barcode-area {
    position: absolute; left: 247px; top: 460px; width: 113px; height: 67px;
    background: #fff; display: flex; align-items: center; justify-content: center;
    font-family: Georgia, serif; font-size: 5px; letter-spacing: 2px; color: #333;
  }
  /* Spine */
  .spine {
    position: relative; width: 40px; height: 100%; background: var(--spine);
    color: var(--spine-text);
  }
  .spine-title {
    position: absolute; top: 22px; left: 50%; transform: translateX(-50%);
    writing-mode: vertical-rl; font-family: "Permanent Marker", cursive;
    font-size: 13px; letter-spacing: 2px;
  }
  .spine-subtitle {
    position: absolute; top: 300px; left: 50%; transform: translateX(-50%);
    writing-mode: vertical-rl; font-family: "Oswald", sans-serif;
    font-size: 6.5px; letter-spacing: 1.2px; text-transform: uppercase;
  }
  /* Front cover */
  .front-cover {
    position: relative; width: 383px; height: 100%; overflow: hidden;
    background: linear-gradient(to bottom, var(--cover-yellow) 0%, #f0d41c 38%, #a9b52c 52%, var(--leaf-green) 64%, #3f6f4e 80%, var(--road-teal) 100%);
  }
  .front-title { position: absolute; left: 20px; right: 14px; font-family: "Permanent Marker", cursive; line-height: 1; }
  .title-line-one { top: 22px; font-size: 47px; color: var(--title-blue); letter-spacing: 0.5px; transform: skewX(-6deg); }
  .title-line-two { top: 78px; font-size: 44px; color: var(--ink); letter-spacing: 5px; transform: skewX(-8deg); }
  .subtitle-band {
    position: absolute; left: 30px; top: 158px; width: 335px; height: 70px;
    background: var(--band-olive); border-radius: 6px; transform: rotate(-5deg);
  }
  .subtitle {
    position: absolute; left: 80px; top: 160px; width: 250px; transform: rotate(-8deg);
    font-family: "Permanent Marker", cursive; color: #fff; text-align: center;
    font-size: 16px; line-height: 18px; text-transform: uppercase;
  }
  .author {
    position: absolute; left: 0; right: 0; top: 506px; text-align: center;
    font-family: "Oswald", sans-serif; font-weight: 600; font-size: 21px;
    letter-spacing: 5px; color: var(--author-yellow); text-transform: uppercase;
  }
</style>
</head>
<body>
<main class="spread">
  <section class="back-cover">
    <div class="back-photo" role="img" aria-label="Faded photo of a motorbike dashboard on a Vietnamese road, with a faint map of Vietnam behind the text"></div>
    <div class="back-content">
      <h2 class="back-headline"><strong>Travel like a pro</strong> in a country<br>where bribing cops is <strong>normal!</strong></h2>
      <p class="synopsis">Everyone knows someone who's ridden the length of Vietnam. What if you could do the same? For us Kiwis and Australians, it's difficult finding decent material about motorcycling in Vietnam. With so much conflicting information online and uncertainty around costs, it's no wonder people keep putting off this 1600 km road trip.</p>
      <p class="synopsis">Dec Ashworth has been there and done it. In the flesh. And whether your goal is riding from Saigon to Hanoi, across multiple Southeast Asian countries, or just hooning around for a few days, this guide is your bulletproof vest.</p>
      <h3 class="reveals-heading">This step - by - step wanderer's manual reveals:</h3>
      <ul class="reveal-list">
        <li>How to plan your own motorcycle odyssey before leaving home</li>
        <li>Where and how to buy / rent a bike</li>
        <li>What types of licences and insurance you'll need</li>
        <li>How to finish your trip alive without getting shaken down by dodgy cops or run over by a pig truck</li>
        <li>Itemized expense reports, showing this journey is possible for as little as $90 NZD per day and even as low as $50.</li>
        <li>A day-by-day outline of our riding itinerary</li>
      </ul>
      <p class="closing">None of us are getting any younger. And with all the information you need in one lightweight book, what's stopping you?</p>
      <p class="paradise">This place is a paradise!</p>
    </div>
    <div class="flags">
      <svg class="flag" viewBox="0 0 33 20" role="img" aria-label="Flag of Vietnam">
        <rect width="33" height="20" fill="var(--flag-red)"/>
        <polygon fill="#ffde00" points="16.5,4 17.9,8.3 22.4,8.3 18.8,11 20.1,15.3 16.5,12.6 12.9,15.3 14.2,11 10.6,8.3 15.1,8.3"/>
      </svg>
      <svg class="flag" viewBox="0 0 33 20" role="img" aria-label="Flag of New Zealand">
        <rect width="33" height="20" fill="var(--flag-blue)"/>
        <g stroke="#fff" stroke-width="2"><line x1="0" y1="0" x2="16" y2="10"/><line x1="16" y1="0" x2="0" y2="10"/></g>
        <g stroke="#fff" stroke-width="3"><line x1="8" y1="0" x2="8" y2="10"/><line x1="0" y1="5" x2="16" y2="5"/></g>
        <g stroke="var(--flag-red)" stroke-width="1.5"><line x1="8" y1="0" x2="8" y2="10"/><line x1="0" y1="5" x2="16" y2="5"/></g>
        <g fill="var(--flag-red)" stroke="#fff" stroke-width="0.4">
          <circle cx="25" cy="5" r="1.2"/><circle cx="22" cy="10" r="1.2"/><circle cx="28" cy="9" r="1.2"/><circle cx="25" cy="16" r="1.3"/>
        </g>
      </svg>
    </div>
    <p class="site">meridianrides.net</p>
    <p class="genre">TRAVEL GUIDE</p>
    <div class="barcode-area">BARCODE AREA</div>
  </section>

  <section class="spine">
    <p class="spine-title">THROTTLE MERIDIAN</p>
    <p class="spine-subtitle">A Wanderer's Manual for Crossing the Breadth of Vietnam</p>
  </section>

  <section class="front-cover" role="img" aria-label="Photo: two riders on a scooter on a green hillside road in Vietnam, one raising an arm, shot from a selfie stick">
    <h1>
      <span class="front-title title-line-one">THROTTLE</span>
      <span class="front-title title-line-two">MERIDIAN</span>
    </h1>
    <div class="subtitle-band"></div>
    <p class="subtitle">A Wanderer's Manual<br>for Crossing the<br>Breadth of Vietnam</p>
    <p class="author">Declan Ashworth</p>
  </section>
</main>
</body>
</html>
```